Business Card Design Project

Business Card
We are rebranding with a new logo
Industry/Entity Type
Business
Contact Information for Business Card
Dennis Morvale +61 487215963 dennis@quorv.com.au P.O. Box 872 Fernlow QLD 4309
Requirements
Must have
- Logo

```html
<!DOCTYPE html>
<html lang="en">
<head>
<meta charset="utf-8">
<title>Quorv International — Business Card</title>
<link rel="stylesheet" href="https://fonts.googleapis.com/css2?family=Fira+Sans:wght@300;400;600&display=swap">
<style>
  :root {
    --navy: #46507e;
    --steel: #6f95bf;
    --cyan: #9ffcfc;
    --orange: #f26a1b;
    --orange-deep: #e5471a;
    --edge-blue: #1f6fb6;
    --paper: #ffffff;
    --paper-grey: #e4e4e6;
    --text-light: #ffffff;
    --brand-blue: #1d5fa8;
  }
  * { margin: 0; padding: 0; box-sizing: border-box; }
  html, body { width: 1200px; height: 717px; overflow: hidden; background: #ffffff; }
  .card {
    position: relative;
    width: 1200px;
    height: 717px;
    overflow: hidden;
    font-family: "Fira Sans", Arial, sans-serif;
    background: radial-gradient(ellipse 620px 520px at 560px 120px, var(--cyan) 0%, #8fd6e8 35%, var(--steel) 70%, var(--navy) 100%);
  }
  .card__shapes { position: absolute; inset: 0; }
  .contact-holder {
    position: absolute;
    left: 104px;
    top: 190px;
    color: var(--text-light);
  }
  .holder__name {
    font-weight: 600;
    font-size: 43px;
    letter-spacing: 1.5px;
    text-transform: uppercase;
    line-height: 1;
  }
  .holder__title {
    margin-top: 4px;
    margin-left: 92px;
    font-weight: 300;
    font-size: 30px;
    color: var(--orange);
    text-transform: uppercase;
    line-height: 1.05;
  }
  .contact-list {
    position: absolute;
    left: 112px;
    top: 347px;
    list-style: none;
  }
  .contact-list__item {
    position: relative;
    display: flex;
    align-items: flex-start;
    margin-bottom: 20px;
    color: var(--text-light);
    font-weight: 300;
    font-size: 26px;
    line-height: 34px;
  }
  .contact-list__icon {
    flex: none;
    width: 40px;
    height: 40px;
    border-radius: 4px;
    background: var(--orange);
    margin-right: 40px;
    display: flex;
    align-items: center;
    justify-content: center;
  }
  .contact-list__text { padding-top: 4px; }
  .brand {
    position: absolute;
    left: 720px;
    top: 300px;
    width: 330px;
    text-align: center;
    color: var(--brand-blue);
    font-weight: 600;
  }
  .brand__name { font-size: 104px; line-height: 1; letter-spacing: -1px; }
  .brand__sub { margin-top: 10px; font-size: 28px; letter-spacing: 4.5px; }
</style>
</head>
<body>
  <div class="card">
    <svg class="card__shapes" width="1200" height="717" viewBox="0 0 1200 717" aria-hidden="true">
      <defs>
        <linearGradient id="paperGradient" x1="0" y1="0" x2="1" y2="1">
          <stop offset="0" stop-color="var(--paper)"/>
          <stop offset="1" stop-color="var(--paper-grey)"/>
        </linearGradient>
        <linearGradient id="accentGradient" x1="0" y1="0" x2="0" y2="1">
          <stop offset="0" stop-color="var(--orange-deep)"/>
          <stop offset="1" stop-color="#ff8c1a"/>
        </linearGradient>
      </defs>
      <path d="M688,0 C560,30 488,140 528,262 C560,350 610,390 648,450" fill="none" stroke="url(#accentGradient)" stroke-width="34" stroke-linecap="round"/>
      <path d="M648,450 C690,520 702,600 700,717" fill="none" stroke="var(--edge-blue)" stroke-width="12"/>
      <path d="M704,0 C580,32 508,142 546,260 C590,390 706,470 706,717 L1200,717 L1200,0 Z" fill="url(#paperGradient)" role="img" aria-label="Soft grey geometric backdrop"/>
    </svg>

    <div class="contact-holder">
      <p class="holder__name">Dennis Morvale</p>
      <p class="holder__title">Job Title</p>
    </div>

    <ul class="contact-list">
      <li class="contact-list__item">
        <span class="contact-list__icon">
          <svg width="26" height="26" viewBox="0 0 24 24" aria-hidden="true"><path fill="#fff" d="M6.6 10.8c1.4 2.8 3.8 5.1 6.6 6.6l2.2-2.2c.3-.3.7-.4 1-.2 1.1.4 2.3.6 3.6.6.6 0 1 .4 1 1V20c0 .6-.4 1-1 1C10.6 21 3 13.4 3 4c0-.6.4-1 1-1h3.5c.6 0 1 .4 1 1 0 1.3.2 2.5.6 3.6.1.3 0 .7-.2 1z"/></svg>
        </span>
        <span class="contact-list__text">+61 487215963</span>
      </li>
      <li class="contact-list__item">
        <span class="contact-list__icon">
          <svg width="28" height="22" viewBox="0 0 28 22" aria-hidden="true"><rect x="1" y="2" width="22" height="15" fill="none" stroke="#fff" stroke-width="2"/><path d="M1 2l11 9 11-9" fill="none" stroke="#fff" stroke-width="2"/><circle cx="22" cy="16" r="4.5" fill="var(--orange)" stroke="#fff" stroke-width="1.6"/></svg>
        </span>
        <span class="contact-list__text">dennis@quorv.com.au</span>
      </li>
      <li class="contact-list__item">
        <span class="contact-list__icon">
          <svg width="24" height="26" viewBox="0 0 24 26" aria-hidden="true"><path d="M3 10a9 8 0 0 1 18 0v10H3z" fill="#fff"/><rect x="6" y="11" width="12" height="2" fill="var(--orange)"/><rect x="6" y="15" width="12" height="2" fill="var(--orange)"/><rect x="10" y="20" width="4" height="5" fill="#fff"/></svg>
        </span>
        <span class="contact-list__text">P.O. Box 872 Fernlow<br>QLD 4309</span>
      </li>
    </ul>

    <div class="brand">
      <p class="brand__name">Quorv</p>
      <p class="brand__sub">INTERNATIONAL</p>
    </div>
  </div>
</body>
</html>
```